Keystone Trench Co Business Card*

Looking for a professional, clean and crisp business card

I am in the underground utilities industry and am just looking for a really impressive business card. I would like our card to be white with our symbol crisp and clear with it protruding. I also have a business partner that will require his name and info on the card once the design is set. I would like to have our website info on the card which is;
http://keystonetrenchco.example/

Contact Information for Business Card

Website, contact name, number and email

```html
<!DOCTYPE html>
<html lang="en">
<head>
<meta charset="utf-8">
<title>Keystone Trench Co – Business Card</title>
<link href="https://fonts.googleapis.com/css2?family=Oswald:wght@400;600&display=swap" rel="stylesheet">
<style>
  :root {
    --backdrop: #a9adb0;
    --card: #f4f3f0;
    --card-edge: #1f3a8a;
    --ink: #232323;
    --ink-soft: #4e4e4e;
    --accent-blue: #3a63b8;
    --accent-red: #d8262a;
  }
  * { margin: 0; padding: 0; box-sizing: border-box; }
  html, body {
    width: 1200px;
    height: 824px;
    overflow: hidden;
    background: var(--backdrop);
    font-family: "Oswald", "Arial Narrow", sans-serif;
  }
  .canvas {
    position: relative;
    width: 1200px;
    height: 824px;
    display: flex;
    align-items: center;
    justify-content: center;
  }
  .business-card {
    width: 440px;
    height: 770px;
    background: var(--card);
    border-bottom: 3px solid var(--card-edge);
    border-left: 2px solid var(--card-edge);
    box-shadow: 0 6px 18px rgba(0, 0, 0, 0.18);
    display: flex;
    flex-direction: column;
    align-items: center;
    text-align: center;
    text-transform: uppercase;
    padding-top: 120px;
  }
  .brand-mark {
    display: flex;
    flex-direction: column;
    align-items: center;
    gap: 22px;
    height: 230px;
  }
  .brand-mark__circle {
    width: 120px;
    height: 120px;
    border-radius: 50%;
    border: 8px solid var(--ink);
  }
  .brand-mark__name {
    font-weight: 600;
    font-size: 30px;
    letter-spacing: 1px;
    color: var(--ink);
  }
  .person__name {
    margin-top: 30px;
    font-weight: 600;
    font-size: 40px;
    letter-spacing: 1px;
    line-height: 1.1;
    color: var(--accent-blue);
  }
  .person__role {
    font-weight: 600;
    font-size: 19px;
    letter-spacing: 1px;
    color: var(--accent-red);
  }
  .divider {
    width: 24px;
    height: 2px;
    background: var(--accent-blue);
    margin: 14px auto;
  }
  .contact {
    font-weight: 400;
    font-size: 17px;
    line-height: 1.45;
    letter-spacing: 0.6px;
    color: var(--ink-soft);
  }
</style>
</head>
<body>
<main class="canvas">
  <article class="business-card">
    <div class="brand-mark">
      <span class="brand-mark__circle" aria-hidden="true"></span>
      <span class="brand-mark__name">Keystone Trench Co</span>
    </div>

    <h1 class="person__name">Daniel Reyes</h1>
    <p class="person__role">President</p>

    <span class="divider" aria-hidden="true"></span>

    <address class="contact" style="font-style: normal;">
      Keystone Trench Co LLC<br>
      4120 Birchwood Road<br>
      Fairbanks, Alaska 99701
    </address>

    <span class="divider" aria-hidden="true"></span>

    <p class="contact">
      555-214-7730<br>
      info@keystonetrenchco.example<br>
      www.keystonetrenchco.example
    </p>
  </article>
</main>
</body>
</html>
```